Edgey, Modern Air Conditioning Website

Bramble Works
current website - www.kelvaroom.nz
Facebook - www.facebook.com/bramwrk

We really have no idea about webdesign etc we are Engineers not Graphic artists or creative writers. We really just want a edgy, modern website completed on our behalf

We can get pictures of projects as directed or happy for you to use stock images of Talvoro Mecha NZ (Heatpumps) air conditioning and exposed ducting etc

we would like the website to be heavily based on the below website. I like what they have done with both the site and the app but obviously would need to suit Bramble Works, snowflakes heating cooling etc etc Blue and white to match our logo etc

http://parrowbeams.co.nz/

Need links to contact page:
Bramble Works
27 Harlow Crescent
Petone
Wellington

0800 529 174 (0800BRAMWKS)

Marta.k@bramwks.co.nz

BRAMBLE WORKS
SATISFACTION GAURANTEED

WHY CHOOSE BRAMBLE WORKS
EXPERIENCE COUNTS

We have a team of nationally trained and qualified Refrigeration/HVAC/Electrical Engineers and Technicians based in Petone, Wellington offering services to Wellington, Manuwatu and the Wairarapa. We are factory trained and authorised to design, service and install all major brands including Talvoro, Pelnor, Korrowane Electric, Veltrada and Osmelo units. We extend our installation warranty to match that of the manufacturer’s warranty and specialise in our own diagnostics and repair.

SATISFACTION GUARANTEE
We aim to please and I put my name behind our brand! We will take care of your project from start to finish and offer a unique experience with our 100% satisfaction Guarantee*. We will supply and install your system and if your system is not installed how it was explained or not up to a trades standard we will return to make any the necessary modifications free of charge. We back this service up with our 0% upfront strategy, the power is in your hands. We will only invoice you once the installation has been completed up to a BRAMBLE WORKS standard.

LOW PRESSURE SALES
Nobody likes the vacuum salesmen’s techniques and neither do we. We will come to your home or business to provide a free measure and quote. Our experience will insure this is a quick and painless experience, you will be provided with expert advice from a qualified Refrigeration Engineer, not a car salesmen turned “Heating Guru”. We will follow up with an email providing our best price straight up, installation details and online brochures. We won’t bug you with repeated phone calls and inbox clogging emails. Once we receive confirmation we will issue you with an installation date and typically have your installation completed within 10 working days.

BRANDS
www.talvoromecha.co.nz
www.pelnor.co.nz
http://quellaro.co.nz/

SERVICES
Heatpumps/Air Conditioning – Heat pumps are the most efficient way of using electricity to heat your home, but some are more efficient than others. We will select the right model for your requirements taking into account the capacity required, the visual impact of the system, the style of system, air flow and obviously your personal preferences. We only install the highest quality brands that offer outstanding after sales support. Cassettes, Consoles, Under Ceilings, Ducted, Hiwalls, Multis… Confused? Give us a call.

COMMERCIAL
We have a growing Portfolio of clients that rely on us for their Commercial requirements. We have proven ourselves to be a force to be reckoned with to be able to think outside the square and come up with unique and cost effective solutions to heat and cool large areas.

CENTRAL HEATING
Ducted Heatpumps are the holy grail of central heating and guess what? They can also cool and dehumidify your home. Ducted Heatpumps are often overlooked or priced out of reach by less experienced salesmen as its not just a point and shoot approach. We pride ourselves in our work with Ducted systems, we are able to provide quick and economic quotations and can provide expert advice on all the extra options on Ducted systems with zone control, fresh air integration, positive pressure solutions. We use the best materials when it comes to insulated ducting, mounting equipment, drainage materials. Every system we design is designed with the lowest possible decibel reading, least amount of static pressure and maximum effieciency with the help of the very latest software available.

VENTILATION
Home ventilation is a very important part of insuring you have a nice dry home to maximise the efficiency of your Heat pump. Whilst HRV systems are not designed to Heat your house they are designed to keep it dry, provide fresh filtered air to ensure your home healthy and easy to heat. We offer a number of solutions from integrated ducted heatpump systems to balanced heat recovery systems and positive air systems.

TESTIMONIALS
http://www.lotbazaro.co.nz/Browse/Listing.aspx?id=415728306

Target Market(s)

Home Owners

Industry/Entity Type

Air Conditioning

Colors
33a6d7
ffffff

Requirements
Must have
• Could possibly use the 'O' from Bramble Works logo throughout website - see business Card
Nice to have
• Bright & Crisp - White and Blue
• Would love to have our Logo used throughout the website.

```html
<!DOCTYPE html>
<html lang="en">
<head>
<meta charset="utf-8">
<title>Bramble Works – Heating, Cooling &amp; Ventilation</title>
<link rel="stylesheet" href="https://fonts.googleapis.com/css2?family=Oswald:wght@400;500;700&family=Open+Sans:wght@400;600;700&display=swap">
<style>
:root{
  --blue:#33a6d7;
  --blue-soft:#5bbbe3;
  --blue-deep:#1f8fc2;
  --white:#ffffff;
  --ink:#222222;
  --body:#555555;
  --dark:#1b1b1b;
  --darker:#111111;
  --nav:#2a2a2a;
  --field:#4a4a4a;
  --grey:#f1f1f1;
  --grey-mid:#dcdcdc;
}
*{box-sizing:border-box;margin:0;padding:0}
html,body{width:1200px;height:3557px;overflow:hidden}
body{font-family:"Open Sans",Arial,sans-serif;color:var(--body);background:var(--white)}
.display{font-family:"Oswald","Arial Narrow",sans-serif;font-weight:700;text-transform:uppercase}

/* header */
.site-header{position:relative;height:630px;overflow:hidden}
.hero-bg{position:absolute;inset:0;background:linear-gradient(180deg,#2b2b2b 0%,#161616 55%,#0d0d0d 100%)}
.topbar{position:relative;height:100px;display:flex;align-items:center;justify-content:space-between;padding:0 130px;background:rgba(0,0,0,.35)}
.brand-name{font-family:"Oswald","Arial Narrow",sans-serif;font-weight:700;color:var(--blue);font-size:38px;letter-spacing:1px;line-height:1}
.call{display:flex;align-items:center;gap:14px;color:var(--white)}
.call small{display:block;font-size:15px}
.call strong{display:block;font-family:"Oswald","Arial Narrow",sans-serif;font-weight:400;font-size:30px;line-height:1.1}
.main-nav{position:relative;height:35px;background:var(--nav);display:flex;align-items:center;padding-left:130px}
.main-nav a{display:flex;align-items:center;gap:8px;color:var(--white);text-decoration:none;font-size:12px;font-weight:700;text-transform:uppercase;width:178px}
.main-nav a.active{color:var(--blue)}
.main-nav svg{width:13px;height:13px}
.hero{position:relative;text-align:center;color:var(--white);padding-top:62px}
.hero h1{font-size:42px;line-height:1.1;color:var(--blue-soft);font-weight:500}
.hero .tag{font-size:24px;font-weight:500;margin-top:2px}
.hero h2{font-size:24px;font-weight:500;margin-top:34px}
.hero-form{width:676px;margin:34px auto 0;display:grid;grid-template-columns:1fr 1fr 1fr;gap:10px 8px}
.field{height:48px;background:var(--field);border:1px solid #666;color:#ddd;font-size:12px;text-align:left;padding:12px 10px}
.hero-form .field.message{grid-column:1/4;height:90px}
.btn{display:inline-block;background:var(--blue);color:var(--white);font-weight:700;font-size:13px;text-transform:uppercase;text-align:center}
.hero .btn{width:159px;height:40px;line-height:40px;margin-top:40px}

/* why */
.why{height:540px;overflow:hidden;text-align:center;padding-top:40px}
.section-title{font-size:28px;color:var(--blue);font-weight:500;display:inline-block;padding-bottom:10px;border-bottom:3px solid var(--blue)}
.why-grid{width:950px;margin:30px auto 0;display:grid;grid-template-columns:repeat(3,1fr);gap:24px}
.why-grid svg{height:80px;width:80px}
.why-grid h3{font-size:16px;color:var(--ink);text-transform:uppercase;margin:20px 0 8px}
.why-grid p{font-size:10px;line-height:1.4;text-align:justify}

/* brands */
.brands{height:372px;background:linear-gradient(180deg,var(--blue) 0 168px,var(--grey-mid) 168px);text-align:center;padding-top:78px}
.brands .section-title{color:var(--white);border-color:var(--white)}
.brand-row{display:grid;grid-template-columns:repeat(3,1fr);gap:9px;padding:0 5px;margin-top:30px}
.brand-card{height:203px;background:var(--white);display:flex;align-items:center;justify-content:center;gap:12px;font-family:"Oswald","Arial Narrow",sans-serif;font-weight:500;font-size:30px;color:#333;text-transform:uppercase}
.brand-card i{width:22px;height:22px;background:var(--blue);display:block}

/* services */
.services{height:796px;overflow:hidden;text-align:center;padding-top:36px}
.services .intro{width:940px;margin:20px auto 0;font-size:11px;line-height:1.5}
.service-grid{width:944px;margin:20px auto 0;display:grid;grid-template-columns:repeat(3,1fr);gap:9px}
.service{background:var(--grey);height:589px}
.service .photo{height:221px}
.photo.plant{background:linear-gradient(160deg,#8fb3cc,#4d6f86 60%,#2e4455)}
.photo.tech{background:linear-gradient(160deg,#8b8b86,#5c5d5a 60%,#3a3b3a)}
.photo.roof{background:linear-gradient(180deg,#c9d2d8,#8e989e 60%,#5b6369)}
.service h3{font-size:16px;color:var(--ink);text-transform:uppercase;margin:24px 0 12px}
.service p{font-size:11px;line-height:1.5;text-align:justify;padding:0 24px}

/* testimonials */
.testimonials{height:439px;margin-top:19px;background:var(--blue);position:relative;text-align:center;padding-top:52px}
.testimonials .section-title{color:var(--white);border-color:var(--white)}
.quotes{position:absolute;left:142px;right:156px;top:184px;display:grid;grid-template-columns:1fr 1fr;gap:50px}
.quote{background:var(--blue-soft);height:207px;padding:20px 24px 0 76px;text-align:left;color:var(--white);position:relative}
.quote::before{content:"\201C";position:absolute;left:22px;top:-6px;font-family:Georgia,serif;font-size:76px;line-height:1}
.quote::after{content:"\201D";position:absolute;right:40px;top:118px;font-family:Georgia,serif;font-size:76px;line-height:1}
.quote p{font-size:11px;line-height:1.5}
.quote cite{display:block;font-style:normal;font-weight:700;font-size:12px;margin-top:12px;padding-bottom:6px;border-bottom:1px solid var(--white);width:100px}
.quote small{font-size:9px}
.arrow{position:absolute;top:326px;width:20px;height:40px}
.arrow.prev{left:78px}.arrow.next{right:78px}

/* contact */
.contact{height:489px;background:linear-gradient(180deg,#262626,#181818);color:var(--white);text-align:center;padding-top:44px}
.contact .section-title{color:var(--white);border-color:var(--white)}
.contact-cols{display:grid;grid-template-columns:1fr 1fr;padding:0 130px;margin-top:40px;text-align:left;gap:130px}
.contact h4{font-size:15px;font-weight:700;text-transform:uppercase;margin-bottom:18px}
.address{font-size:13px;line-height:1.45}
.address b{font-weight:700}
.chips{margin-top:24px;display:grid;gap:12px}
.chip{width:258px;height:38px;background:var(--blue);display:flex;align-items:center;gap:10px;padding-left:12px;font-size:14px;font-weight:700}
.chip svg{width:16px;height:16px}
.contact-form{display:flex;flex-direction:column;gap:10px}
.contact-form .field{height:40px;background:#3a3a3a;border-color:#555;font-size:10px;padding:12px 10px}
.contact-form .field.message{height:80px}
.contact-form .btn{align-self:flex-end;width:138px;height:32px;line-height:32px;font-size:12px;margin-top:4px}

/* footer */
.site-footer{height:225px;margin-top:35px;background:var(--dark);display:flex;align-items:center;justify-content:space-between;padding:0 130px 30px}
.site-footer .main-nav{background:none;padding:0;height:auto}
.site-footer .main-nav a{width:auto;margin-left:38px;font-size:11px}
.copyright{height:47px;background:var(--darker);color:#bbb;font-size:11px;text-align:center;line-height:47px;margin-top:-36px;position:relative}
</style>
</head>
<body>

<header class="site-header">
  <div class="hero-bg" role="img" aria-label="Dark industrial warehouse interior with exposed ducting"></div>
  <div class="topbar">
    <span class="brand-name">BRAMBLE WORKS</span>
    <div class="call">
      <svg width="26" height="42" viewBox="0 0 26 42"><rect x="2" y="2" width="22" height="38" rx="3" fill="none" stroke="#fff" stroke-width="3"/><circle cx="13" cy="34" r="2" fill="#fff"/></svg>
      <div><small>Call us now :</small><strong>0800 529 174</strong></div>
    </div>
  </div>
  <nav class="main-nav">
    <a class="active"><svg viewBox="0 0 14 14"><path d="M1 7 7 1l6 6h-2v6H9V9H5v4H3V7z" fill="currentColor"/></svg>Home</a>
    <a><svg viewBox="0 0 14 14"><circle cx="7" cy="4" r="3" fill="currentColor"/><path d="M1 14c0-4 3-6 6-6s6 2 6 6z" fill="currentColor"/></svg>About Us</a>
    <a><svg viewBox="0 0 14 14"><circle cx="7" cy="7" r="4" fill="none" stroke="currentColor" stroke-width="3"/></svg>Services</a>
    <a><svg viewBox="0 0 14 14"><path d="M1 2h12v8H5l-3 3v-3H1z" fill="currentColor"/></svg>Testimonials</a>
    <a><svg viewBox="0 0 14 14"><path d="M1 1h6l6 6-6 6-6-6z" fill="currentColor"/></svg>Brands</a>
    <a><svg viewBox="0 0 14 14"><path d="M1 3h12v9H1z" fill="currentColor"/></svg>Contact Us</a>
  </nav>
  <div class="hero">
    <h1 class="display">Bramble Works</h1>
    <p class="tag display">Satisfaction Gauranteed</p>
    <h2 class="display">Get in touch</h2>
    <div class="hero-form">
      <div class="field">Full Name</div>
      <div class="field">E mail</div>
      <div class="field">Ph.No</div>
      <div class="field message">Message</div>
    </div>
    <span class="btn">Send Message</span>
  </div>
</header>

<section class="why">
  <h2 class="section-title display">Why choose Bramble Works</h2>
  <div class="why-grid">
    <article>
      <svg viewBox="0 0 96 96" fill="none" stroke="#33a6d7" stroke-width="3"><rect x="22" y="12" width="52" height="72" rx="6"/><rect x="32" y="26" width="12" height="12"/><path d="M34 32l3 3 5-6"/><path d="M52 32h14"/><rect x="32" y="50" width="12" height="12"/><path d="M34 56l3 3 5-6"/><path d="M52 56h14"/></svg>
      <h3>Experience Counts</h3>
      <p>We have a team of nationally trained and qualified Refrigeration/HVAC/Electrical Engineers and Technicians based in Petone, Wellington offering services to Wellington, Manuwatu and the Wairarapa. We are factory trained and authorised to design, service and install all major brands including Talvoro, Pelnor, Korrowane Electric, Veltrada and Osmelo units. We extend our installation warranty to match that of the manufacturer’s warranty and specialise in our own diagnostics and repair.</p>
    </article>
    <article>
      <svg viewBox="0 0 96 96" fill="none" stroke="#33a6d7" stroke-width="3"><circle cx="48" cy="40" r="26"/><circle cx="48" cy="40" r="18"/><path d="M38 40l7 7 13-14"/><path d="M30 60 20 86l12-4 6 10 10-24"/><path d="M66 60l10 26-12-4-6 10-10-24"/></svg>
      <h3>Satisfaction Guarantee</h3>
      <p>We aim to please and I put my name behind our brand! We will take care of your project from start to finish and offer a unique experience with our 100% satisfaction Guarantee*. We will supply and install your system and if your system is not installed how it was explained or not up to a trades standard we will return to make any the necessary modifications free of charge. We back this service up with our 0% upfront strategy, the power is in your hands. We will only invoice you once the installation has been completed up to a BRAMBLE WORKS standard.</p>
    </article>
    <article>
      <svg viewBox="0 0 96 96" fill="none" stroke="#33a6d7" stroke-width="3"><rect x="18" y="52" width="12" height="34"/><rect x="38" y="62" width="12" height="24"/><rect x="58" y="72" width="12" height="14"/><path d="M16 16l58 42"/><path d="M62 58h14V44"/></svg>
      <h3>Low Pressure Sales</h3>
      <p>Nobody likes the vacuum salesmen’s techniques and neither do we. We will come to your home or business to provide a free measure and quote. Our experience will insure this is a quick and painless experience, you will be provided with expert advice from a qualified Refrigeration Engineer, not a car salesmen turned “Heating Guru”. We will follow up with an email providing our best price straight up, installation details and online brochures. We won’t bug you with repeated phone calls and inbox clogging emails. Once we receive confirmation we will issue you with an installation date and typically have your installation completed within 10 working days.</p>
    </article>
  </div>
</section>

<section class="brands">
  <h2 class="section-title display">Our Brands</h2>
  <div class="brand-row">
    <div class="brand-card">Talvoro Mecha</div>
    <div class="brand-card">Pelnor</div>
    <div class="brand-card">Quellaro <i></i></div>
  </div>
</section>

<section class="services">
  <h2 class="section-title display">Our Services</h2>
  <p class="intro">Heatpumps/Air Conditioning – Heat pumps are the most efficient way of using electricity to heat your home, but some are more efficient than others. We will select the right model for your requirements taking into account the capacity required, the visual impact of the system, the style of system, air flow and obviously your personal preferences. We only install the highest quality brands that offer outstanding after sales support. Cassettes, Consoles, Under Ceilings, Ducted, Hiwalls, Multis… Confused? Give us a call.</p>
  <div class="service-grid">
    <article class="service">
      <div class="photo plant" role="img" aria-label="Commercial plant with large pipework under a blue sky"></div>
      <h3>Commercial</h3>
      <p>We have a growing Portfolio of clients that rely on us for their Commercial requirements. We have proven ourselves to be a force to be reckoned with to be able to think outside the square and come up with unique and cost effective solutions to heat and cool large areas.</p>
    </article>
    <article class="service">
      <div class="photo tech" role="img" aria-label="Technician working on a central heating unit"></div>
      <h3>Central Heating</h3>
      <p>Ducted Heatpumps are the holy grail of central heating and guess what? They can also cool and dehumidify your home. Ducted Heatpumps are often overlooked or priced out of reach by less experienced salesmen as its not just a point and shoot approach. We pride ourselves in our work with Ducted systems, we are able to provide quick and economic quotations and can provide expert advice on all the extra options on Ducted systems with zone control, fresh air integration, positive pressure solutions. We use the best materials when it comes to insulated ducting, mounting equipment, drainage materials. Every system we design is designed with the lowest possible decibel reading, least amount of static pressure and maximum effieciency with the help of the very latest software available.</p>
    </article>
    <article class="service">
      <div class="photo roof" role="img" aria-label="Rows of roof ventilation turbines"></div>
      <h3>Ventilation</h3>
      <p>Home ventilation is a very important part of insuring you have a nice dry home to maximise the efficiency of your Heat pump. Whilst HRV systems are not designed to Heat your house they are designed to keep it dry, provide fresh filtered air to ensure your home healthy and easy to heat. We offer a number of solutions from integrated ducted heatpump systems to balanced heat recovery systems and positive air systems.</p>
    </article>
  </div>
</section>

<section class="testimonials">
  <h2 class="section-title display">Testimonials</h2>
  <svg class="arrow prev" viewBox="0 0 20 40"><path d="M17 2 3 20l14 18" fill="none" stroke="#fff" stroke-width="3"/></svg>
  <div class="quotes">
    <blockquote class="quote">
      <p>Team Bramble are amazing! Renna on admin is super friendly &amp; organised everything effortlessly, Marta &amp; Tomas were very professional, gave great advice and really made the whole process easy. I was stoked with the price, and the quality of the product, workmanship and service really impressed me, I will recommend Bramble to all my friends &amp; family.</p>
      <cite>harbour_kid</cite><small>England</small>
    </blockquote>
    <blockquote class="quote">
      <p>Marta and her team are friendly and professional and supplied and installed a high quality heat pump. The whole experience was so easy and the customised service appreciated. I contacted them to check if I could have a heat pump installed at a future date which they happily accommodated. Pricing was also very competitive. Highly recommended!</p>
      <cite>quilm</cite><small>England</small>
    </blockquote>
  </div>
  <svg class="arrow next" viewBox="0 0 20 40"><path d="M3 2l14 18L3 38" fill="none" stroke="#fff" stroke-width="3"/></svg>
</section>

<section class="contact">
  <h2 class="section-title display">Contact Us</h2>
  <div class="contact-cols">
    <div>
      <h4>Request a Quote</h4>
      <p class="address"><b>Bramble Works</b><br>27 Harlow Crescent<br>Petone<br>Wellington</p>
      <div class="chips">
        <div class="chip"><svg viewBox="0 0 16 16"><path d="M3 1l3 3-2 2c1 2 3 4 5 5l2-2 3 3-2 3C6 15 1 10 1 3z" fill="#fff"/></svg>: 0800 529 174</div>
        <div class="chip"><svg viewBox="0 0 16 16"><rect x="1" y="3" width="14" height="10" fill="#fff"/><path d="M1 3l7 6 7-6" fill="none" stroke="#33a6d7" stroke-width="1.5"/></svg>: Marta.k@bramwks.co.nz</div>
        <div class="chip"><svg viewBox="0 0 16 16" fill="none" stroke="#fff" stroke-width="1.5"><circle cx="8" cy="8" r="6.5"/><ellipse cx="8" cy="8" rx="3" ry="6.5"/><path d="M1.5 8h13"/></svg>: www.kelvaroom.nz</div>
      </div>
    </div>
    <div>
      <h4>Contact Form</h4>
      <div class="contact-form">
        <div class="field">Name</div>
        <div class="field">E-mail</div>
        <div class="field">Subject</div>
        <div class="field message">Message</div>
        <span class="btn">Send Message</span>
      </div>
    </div>
  </div>
</section>

<footer class="site-footer">
  <span class="brand-name">BRAMBLE WORKS</span>
  <nav class="main-nav">
    <a class="active">Home</a>
    <a>About Us</a>
    <a>Services</a>
    <a>Testimonials</a>
    <a>Brands</a>
    <a>Contact Us</a>
  </nav>
</footer>
<p class="copyright">Copyrights © 2016 All Rights Reserved</p>

</body>
</html>
```